I have a logo and need to design the business card and stationery.
Updates

The uploaded logo image named as GREYMARSH CONSTRUCTION which is to be replaced to GREYMARSH CONTRACTS. Kindly add below details and submit the designs- Company name- Greymarsh Engineering Contracts LLP Name & Post- Kelvan Joshi (Designated Partner) Address- Block No.317, Wing C, Tulvo Trade Court, Manek Pural Road, Ruparel Industrial Estate, Goregaon(E), Mumbai - 400 063 Contact- +91 97415 60382 Email- kelvanjoshi@mailbrook.example Website- www.greymarshcontracts.example Contact for Letterhead- +91-22-28754193

Hi Tovin Rahul, We are liking your Design #28860835. We have suggested some changes which are mentioned in feedback. Kindly revert with it asap to finalize this design.

Colors

Designer to choose colors to be used in the design.

```html
<!DOCTYPE html>
<html lang="en">
<head>
<meta charset="utf-8">
<title>Greymarsh Contracts – Business Card</title>
<link href="https://fonts.googleapis.com/css2?family=Didact+Gothic&family=Mulish:wght@400;800&display=swap" rel="stylesheet">
<style>
  :root {
    --backdrop: #d8d6d3;
    --card-dark: #141414;
    --card-light: #f1f1f0;
    --ink: #1b1b1b;
    --ink-soft: #333333;
    --rule: #4a4a4a;
    --paper-white: #f4f4f4;
  }
  html, body {
    margin: 0;
    padding: 0;
    width: 1200px;
    height: 1014px;
    overflow: hidden;
    background: var(--backdrop);
  }
  .canvas {
    position: relative;
    width: 1200px;
    height: 1014px;
  }
  .card {
    position: absolute;
    left: 338px;
    width: 524px;
    height: 290px;
    box-shadow: 0 6px 14px rgba(0,0,0,0.25);
  }
  .card--front {
    top: 208px;
    background: var(--card-dark);
    display: flex;
    align-items: center;
    justify-content: center;
    gap: 14px;
  }
  .front-square {
    width: 30px;
    height: 30px;
    background: var(--paper-white);
  }
  .front-name {
    font-family: "Didact Gothic", sans-serif;
    color: var(--paper-white);
    font-size: 34px;
    letter-spacing: 4px;
  }
  .card--back {
    top: 516px;
    background: var(--card-light);
  }
  .brand {
    position: absolute;
    top: 26px;
    right: 38px;
    width: 250px;
    text-align: center;
    font-family: "Didact Gothic", sans-serif;
    color: var(--ink);
  }
  .brand-square {
    width: 52px;
    height: 52px;
    background: var(--ink);
    margin: 0 auto 12px;
  }
  .brand-name {
    font-size: 21px;
    letter-spacing: 2px;
    line-height: 1;
  }
  .brand-sub {
    font-size: 10px;
    letter-spacing: 6px;
    margin-top: 3px;
  }
  .person {
    position: absolute;
    left: 44px;
    top: 142px;
    font-family: "Mulish", sans-serif;
    color: var(--ink);
  }
  .person-name {
    font-size: 20px;
    line-height: 1;
    letter-spacing: 0.3px;
  }
  .person-name strong { font-weight: 800; }
  .person-name span { font-weight: 400; }
  .person-role {
    font-size: 11px;
    margin-top: 3px;
    letter-spacing: 0.3px;
  }
  .rule {
    position: absolute;
    left: 44px;
    right: 0;
    top: 198px;
    height: 1px;
    background: var(--rule);
  }
  .rule-accent {
    position: absolute;
    left: 44px;
    top: 197px;
    width: 141px;
    height: 4px;
    background: var(--ink);
  }
  .contacts, .address {
    position: absolute;
    top: 210px;
    font-family: "Didact Gothic", sans-serif;
    color: var(--ink-soft);
    list-style: none;
    margin: 0;
    padding: 0;
  }
  .contacts { left: 44px; font-size: 11.5px; }
  .contacts li {
    display: flex;
    align-items: center;
    gap: 6px;
    height: 17px;
  }
  .icon { width: 10px; height: 10px; flex: none; }
  .address {
    left: 264px;
    font-size: 10px;
    line-height: 17px;
    display: flex;
    gap: 5px;
  }
  .address .icon { margin-top: 3px; }
</style>
</head>
<body>
<main class="canvas">
  <section class="card card--front">
    <div class="front-square"></div>
    <div class="front-name">GREYMARSH</div>
  </section>

  <section class="card card--back">
    <div class="brand">
      <div class="brand-square"></div>
      <div class="brand-name">GREYMARSH</div>
      <div class="brand-sub">CONTRACTS</div>
    </div>

    <div class="person">
      <div class="person-name"><strong>KELVAN</strong> <span>JOSHI</span></div>
      <div class="person-role">(DESIGNATED PARTNER)</div>
    </div>

    <div class="rule"></div>
    <div class="rule-accent"></div>

    <ul class="contacts">
      <li>
        <svg class="icon" viewBox="0 0 10 10"><circle cx="5" cy="5" r="5" fill="#1b1b1b"/><path d="M3 2.4 L4.1 2.2 L4.6 3.6 L3.9 4.1 Q4.5 5.5 5.9 6.1 L6.4 5.4 L7.8 5.9 L7.6 7 Q4.5 7.4 3 2.4Z" fill="#f1f1f0"/></svg>
        +91 97415 60382
      </li>
      <li>
        <svg class="icon" viewBox="0 0 10 10"><circle cx="5" cy="5" r="5" fill="#1b1b1b"/><rect x="2.4" y="3.2" width="5.2" height="3.6" fill="none" stroke="#f1f1f0" stroke-width="0.7"/><path d="M2.4 3.2 L5 5.2 L7.6 3.2" fill="none" stroke="#f1f1f0" stroke-width="0.7"/></svg>
        kelvanjoshi@mailbrook.example
      </li>
      <li>
        <svg class="icon" viewBox="0 0 10 10"><circle cx="5" cy="5" r="4.5" fill="none" stroke="#1b1b1b" stroke-width="1"/><ellipse cx="5" cy="5" rx="2" ry="4.5" fill="none" stroke="#1b1b1b" stroke-width="0.7"/><path d="M0.5 5 H9.5" stroke="#1b1b1b" stroke-width="0.7"/></svg>
        www.greymarshcontracts.example
      </li>
    </ul>

    <div class="address">
      <svg class="icon" viewBox="0 0 10 10"><circle cx="5" cy="5" r="5" fill="#1b1b1b"/><path d="M5 2 A2 2 0 0 1 7 4 Q7 5.5 5 8 Q3 5.5 3 4 A2 2 0 0 1 5 2Z" fill="#f1f1f0"/><circle cx="5" cy="4" r="0.8" fill="#1b1b1b"/></svg>
      <div>
        Block No.317, Wing C, Tulvo Trade Court,<br>
        Manek Pural Road, Ruparel Industrial Estate,<br>
        Goregaon(E), Mumbai - 400 063
      </div>
    </div>
  </section>
</main>
</body>
</html>
```